Homemaking training schools needs a Business Card design

Designer, Hello!

No special requirements, good-looking enough.
--------------------------------------------------------------------------

Name: Marcus Dole
Chairman
Tel: 0574-71948263
Mobile: 13857420916
Email: kelvora@mailnest.example
Web: www.prt2019.example
Add: No.258, LanpingJie, BeiyuanQu, Ningbo, Zhejiang

LOGO
Ningbo PRT Homemaking Training School

Target Market(s)

pregnant women, mothers, infants, the elderly and families, including cleaning, cooking, nursing training.

Industry/Entity Type

Business

Contact Information for Business Card

Name: Marcus Dole
Chairman
Tel: 0574-71948263
Mobile: 13857420916
Email: kelvora@mailnest.example
Web: www.prt2019.example

LOGO

Font styles to use
Serif
Sans Serif
Decorative

Requirements
Nice to have
• Feels: clean, specifications, safety, comfort, warmth and happiness.

```html
<!DOCTYPE html>
<html lang="en">
<head>
<meta charset="utf-8">
<title>Ningbo PRT Homemaking Training School Business Card</title>
<link rel="stylesheet" href="https://fonts.googleapis.com/css2?family=Lato:wght@300;400;700&family=Quicksand:wght@400;500;600&display=swap">
<style>
  :root {
    --paper: #ffffff;
    --ink: #3b3f45;
    --accent-red: #e8333b;
    --brand-blue: #2f7cf6;
    --icon-bg: #3f4349;
    --band-light: #dcded6;
    --band-dark: #bcc6bc;
    --deco: #eef1f0;
  }
  * { margin: 0; padding: 0; box-sizing: border-box; }
  html, body { width: 1200px; height: 720px; overflow: hidden; background: var(--paper); }
  .card {
    position: relative; width: 1200px; height: 720px; overflow: hidden;
    background: var(--paper); font-family: "Lato", sans-serif; color: var(--ink);
  }
  .backdrop-shape {
    position: absolute; left: 0; top: 0; width: 570px; height: 545px;
    background: radial-gradient(ellipse at 42% 45%, var(--deco) 0%, var(--deco) 45%, rgba(238,241,240,0) 78%);
  }
  .brand { position: absolute; left: 610px; top: 222px; width: 470px; text-align: center; }
  .brand-name {
    font-family: "Quicksand", sans-serif; font-weight: 600; font-size: 64px;
    line-height: 1; color: var(--brand-blue); letter-spacing: 0.5px;
  }
  .brand-tagline {
    display: flex; align-items: center; gap: 12px; margin-top: 12px;
    font-family: "Quicksand", sans-serif; font-weight: 500; font-size: 24px; color: var(--ink);
    white-space: nowrap;
  }
  .brand-tagline::before, .brand-tagline::after {
    content: ""; flex: 1; height: 2px; background: var(--ink);
  }
  .person { position: absolute; right: 724px; top: 410px; text-align: right; }
  .person-name { font-size: 50px; line-height: 1; letter-spacing: -0.5px; white-space: nowrap; }
  .person-name .first { font-weight: 700; color: var(--ink); }
  .person-name .last { font-weight: 300; color: var(--accent-red); }
  .person-role { font-weight: 300; font-size: 27px; letter-spacing: 0.5px; margin-top: 4px; }
  .divider { position: absolute; left: 492px; top: 379px; width: 2px; height: 132px; background: var(--ink); }
  .contact {
    position: absolute; display: flex; align-items: center; gap: 10px;
    font-weight: 400; font-size: 27px; color: var(--ink); white-space: nowrap;
  }
  .contact-icon {
    width: 34px; height: 34px; border-radius: 6px; background: var(--icon-bg);
    display: flex; align-items: center; justify-content: center; flex: none;
  }
  .contact-icon svg { width: 22px; height: 22px; }
  .band-location {
    position: absolute; left: 0; top: 544px; width: 1200px; height: 97px; background: var(--band-light);
  }
  .location-label {
    position: absolute; left: 79px; top: 16px; font-size: 26px;
    letter-spacing: 0.3px; color: var(--ink); white-space: nowrap;
  }
  .location-label strong { font-weight: 700; margin-right: 16px; }
  .location-label span { font-weight: 400; }
  .band-base { position: absolute; left: 0; top: 641px; width: 1200px; height: 79px; background: var(--band-dark); }
</style>
</head>
<body>
<main class="card">
  <div class="backdrop-shape" role="img" aria-label="Large faint decorative shape in pale grey"></div>

  <div class="brand">
    <div class="brand-name">Ningbo PRT</div>
    <div class="brand-tagline">Homemaking Training School</div>
  </div>

  <div class="person">
    <div class="person-name"><span class="first">Marcus</span> <span class="last">Dole</span></div>
    <div class="person-role">CHAIRMAN</div>
  </div>

  <div class="divider"></div>

  <div class="contact" style="left:515px; top:427px;">
    <span class="contact-icon"><svg viewBox="0 0 24 24" fill="#fff"><rect x="3" y="3" width="6" height="18" rx="2"/><rect x="10" y="5" width="11" height="16" rx="2"/><rect x="12" y="8" width="7" height="3" fill="#3f4349"/><circle cx="13.5" cy="14" r="1" fill="#3f4349"/><circle cx="17.5" cy="14" r="1" fill="#3f4349"/><circle cx="13.5" cy="18" r="1" fill="#3f4349"/><circle cx="17.5" cy="18" r="1" fill="#3f4349"/></svg></span>
    <span>0574-71948263</span>
  </div>
  <div class="contact" style="left:515px; top:477px;">
    <span class="contact-icon"><svg viewBox="0 0 24 24" fill="#fff"><rect x="6" y="2" width="12" height="20" rx="2"/><rect x="8" y="5" width="8" height="12" fill="#3f4349"/><circle cx="12" cy="19.5" r="1" fill="#3f4349"/></svg></span>
    <span>13857420916</span>
  </div>
  <div class="contact" style="left:778px; top:427px;">
    <span class="contact-icon"><svg viewBox="0 0 24 24" fill="none" stroke="#fff" stroke-width="1.6"><circle cx="12" cy="12" r="9"/><ellipse cx="12" cy="12" rx="4" ry="9"/><line x1="3" y1="12" x2="21" y2="12"/><line x1="4.5" y1="7.5" x2="19.5" y2="7.5"/><line x1="4.5" y1="16.5" x2="19.5" y2="16.5"/></svg></span>
    <span>www.prt2019.example</span>
  </div>
  <div class="contact" style="left:778px; top:477px;">
    <span class="contact-icon"><svg viewBox="0 0 24 24" fill="none" stroke="#fff" stroke-width="1.8"><circle cx="12" cy="12" r="3.5"/><path d="M15.5 12v1.5a2.5 2.5 0 0 0 5 0V12a8.5 8.5 0 1 0-3.5 6.9"/></svg></span>
    <span>kelvora@mailnest.example</span>
  </div>

  <section class="band-location">
    <div class="location-label"><strong>LOCATION</strong><span>No.258, LanpingJie, BeiyuanQu, Ningbo, Zhejiang</span></div>
  </section>
  <div class="band-base"></div>
</main>
</body>
</html>
```